Business Card: RW Office Partners - Your organised problem solver

Business Name: RW Office Partners
Website: www.rwofficepartners.com.au
Email: marisol@rwofficepartners.com.au
Mobile: 61 482 907 236
Facebook: @rwofficepartners
Instrgram: @rwofficepartners

Brading Colours:
HEX
#986474
#ddccd3
#7a8498
#c9d8e4
#000000
#ffffff

Tag Line: Your organised problem solver

Link to DRAFT website:
https://deskhelpcollective.wixsite.com/rw-office-partners

About Page from the website:
My name is Marisol Wrenfield, and I would love to assist you to become more productive in your day to day and achieve your business and personal goals.
My mission is to give you time, time to work on the important tasks of your business or to be able to spend more time with your family. I will take on the tasks you don’t have time for, don’t know well or simply don’t like to do.
I have an extensive background in Administration, Tender Coordination, Document Control, WHS and Quality Management working primarily in the Construction, Mining and Corporate World.
I am passionate about being organised, having order and making things in your life (and mine) easier! I love to watch something unfold and grow into something amazing! I am known for being the go-to problem solver, the organiser of all things, producing high standards of work even under pressure. I’m also a confident communicator, and I understand that you’re busy running your business.

Target Market(s)

Small to Medium Business who require assistance in their business by a virtual assistant.

Industry/Entity Type

Virtual Assistant

Contact Information for Business Card

Mobile: 61 482 907 236

Font styles to use
Sans Serif

Colors
ffffff

Requirements
Must have
• Branding Colours as outlined.
Contact Details as outlined.
Logo as provided.
Proper contact details - mobile, facebook, instragm, website.
Simple, Elegant, very clean looking.
Should not have
• Note cute with pictures.
Not too girly as still want to market to construction companies.

```html
<!DOCTYPE html>
<html lang="en">
<head>
<meta charset="utf-8">
<title>RW Office Partners – Business Card</title>
<link href="https://fonts.googleapis.com/css2?family=Montserrat:wght@600&family=Roboto:wght@400;500&display=swap" rel="stylesheet">
<style>
  :root {
    --mauve: #986474;
    --mauve-light: #ddccd3;
    --slate: #7a8498;
    --slate-light: #c9d8e4;
    --ink: #2a2a2a;
    --paper: #f7f7f6;
    --backdrop: #676364;
  }
  * { box-sizing: border-box; margin: 0; padding: 0; }
  html, body { width: 1200px; height: 1200px; overflow: hidden; }
  body {
    background: var(--backdrop);
    font-family: "Roboto", Arial, sans-serif;
    position: relative;
  }
  .card {
    position: absolute;
    width: 712px;
    height: 418px;
    background: var(--paper);
    border-radius: 24px;
    overflow: hidden;
  }
  .card--front { left: 238px; top: 119px; }
  .card--back  { left: 230px; top: 645px; }

  .brand {
    position: absolute;
    display: flex;
    align-items: center;
    font-family: "Montserrat", Arial, sans-serif;
    font-weight: 600;
    color: var(--slate);
    white-space: nowrap;
  }
  .brand__mark { background: var(--mauve); flex: none; }
  .card--front .brand { left: 0; right: 0; top: 150px; justify-content: center; font-size: 50px; gap: 20px; }
  .card--front .brand__mark { width: 44px; height: 44px; }
  .card--back .brand { left: 28px; top: 168px; font-size: 29px; gap: 12px; }
  .card--back .brand__mark { width: 26px; height: 26px; }

  .social-row {
    position: absolute;
    left: 0; right: 0; top: 350px;
    display: flex; justify-content: center; gap: 18px;
    font-size: 18.5px; color: var(--ink);
  }
  .social { display: flex; align-items: center; gap: 9px; }
  .social__dot { width: 16px; height: 16px; border-radius: 3px; background: var(--mauve); }

  .band { position: absolute; bottom: 0; height: 16px; }
  .card--front .band--mauve { left: 0; width: 357px; background: var(--mauve); }
  .card--front .band--slate { left: 357px; right: 0; background: var(--slate); }
  .card--back .band--slate { left: 0; width: 330px; background: var(--slate); }

  .tagline {
    position: absolute;
    right: 0; bottom: 0;
    width: 398px; height: 52px;
    background: var(--mauve);
    clip-path: polygon(30px 0, 100% 0, 100% 100%, 0 100%);
    border-top-left-radius: 18px;
    color: #fff;
    font-size: 17.5px;
    padding: 15px 0 0 68px;
  }

  .person { position: absolute; left: 382px; top: 92px; }
  .person__name { font-weight: 500; font-size: 26px; color: var(--mauve); line-height: 1.1; }
  .person__role { font-size: 17px; color: var(--ink); margin-top: 4px; }

  .contacts { position: absolute; left: 382px; top: 166px; list-style: none; }
  .contacts li {
    display: flex; align-items: center; gap: 12px;
    height: 24.2px; font-size: 17.5px; color: var(--ink);
  }
  .contacts svg, .contacts .social__dot { width: 16px; height: 16px; flex: none; }
</style>
</head>
<body>

<section class="card card--front" aria-label="Card front">
  <div class="brand"><span class="brand__mark"></span>RW Office Partners</div>
  <div class="social-row">
    <span class="social"><span class="social__dot"></span>@rwofficepartners</span>
    <span class="social"><span class="social__dot"></span>@rwofficepartners</span>
  </div>
  <div class="band band--mauve"></div>
  <div class="band band--slate"></div>
</section>

<section class="card card--back" aria-label="Card back">
  <div class="brand"><span class="brand__mark"></span>RW Office Partners</div>

  <div class="person">
    <p class="person__name">Marisol Wrenfield</p>
    <p class="person__role">Virtual Assistant</p>
  </div>

  <ul class="contacts">
    <li>
      <svg viewBox="0 0 16 16" aria-hidden="true"><path fill="#986474" d="M1 5c0-2 3-3 7-3s7 1 7 3v1h-3V4.5H4V6H1zM4 7h8l2 7H2zM8 9a1.8 1.8 0 1 0 0 3.6A1.8 1.8 0 0 0 8 9z"/></svg>
      61 482 907 236
    </li>
    <li>
      <svg viewBox="0 0 16 16" aria-hidden="true"><rect x="1" y="3" width="14" height="10" fill="#986474"/><path d="M1.5 3.5 8 9l6.5-5.5M1.5 12.5 6 8m8.5 4.5L10 8" stroke="#f7f7f6" stroke-width="1.2" fill="none"/></svg>
      marisol@rwofficepartners.com.au
    </li>
    <li>
      <svg viewBox="0 0 16 16" aria-hidden="true"><g fill="none" stroke="#986474" stroke-width="1.3"><circle cx="8" cy="8" r="6.3"/><ellipse cx="8" cy="8" rx="2.7" ry="6.3"/><path d="M1.7 8h12.6M2.8 4.8h10.4M2.8 11.2h10.4"/></g></svg>
      www.rwofficepartners.com.au
    </li>
    <li><span class="social__dot"></span>@rwofficepartners</li>
    <li><span class="social__dot"></span>@rwofficepartners</li>
  </ul>

  <div class="band band--slate"></div>
  <div class="tagline">Your organised problem solver</div>
</section>

</body>
</html>
```